Creative, fresh business card design for Ripplecraft Facades

We need a fresh, creative business card design for Ripplecraft Facades. We are the manufacturer of Ripplecraft Facades in Australia. Wall panels are 2400 x 1200mm panels made from MDF and feature 3D patterns on the face of the panel. The colours to be used are green, silver/grey and white RGB
Red 187
Green 207
Blue 65.

An idea is to possibly use a watermark of one of our designs as a background (like on the "Grids" design on the left hand side of page 2 of our brochure).

Target Market(s)

Interior designers, architects, builders and home renovators

Industry/Entity Type

Business

Contact Information for Business Card

Details to go on the card are:
Our logo (attached),
Slogan: "Decorative panels for interiors and exteriors",
Contact name,
Position,
Mobile phone number,
Business address,
Business phone,
Business fax,
Website and
Email address.

I have attached a few images of our panels and our brochure for reference.

The colours of the business card should feature our logo colours which are: RGB
Red 187
Green 207
Blue 65

Requirements
Must have
• Very modern fonts and design. Some of the designs shown especially the "Prisms" design which is a popular design.
Nice to have
• Creative but simple design. Very contemporary.
Should not have
• Anything ornate or old fashioned.

```html
<!DOCTYPE html>
<html lang="en">
<head>
<meta charset="utf-8">
<title>Ripplecraft Facades – Business Card</title>
<link rel="stylesheet" href="https://fonts.googleapis.com/css2?family=Arimo:wght@400;700&family=Open+Sans:wght@400;600&display=swap">
<style>
  :root {
    --backdrop: #dcdcdc;
    --card: #2a2a2c;
    --card-deep: #1f1f21;
    --ripple-light: #3a3a3d;
    --photo-dark: #171719;
    --photo-mid: #2e2e31;
    --brand-green: rgb(187, 207, 65);
    --silver: #9a9a9e;
    --silver-light: #c4c4c8;
    --white: #ffffff;
  }
  * { box-sizing: border-box; margin: 0; padding: 0; }
  html, body {
    width: 1200px; height: 1000px; overflow: hidden;
    background: var(--backdrop);
  }
  .canvas {
    position: relative; width: 1200px; height: 1000px;
    display: flex; align-items: center; justify-content: center;
  }
  .business-card {
    position: relative; width: 820px; height: 470px;
    border-radius: 34px; overflow: hidden;
    background: var(--card);
    box-shadow: 0 18px 40px rgba(0,0,0,0.28);
    font-family: "Open Sans", sans-serif;
  }
  .ripple-texture {
    position: absolute; left: 0; top: 0; width: 560px; height: 470px;
    background: linear-gradient(160deg, var(--ripple-light) 0%, var(--card) 45%, var(--card-deep) 100%);
  }
  .interior-photo {
    position: absolute; right: 0; top: 0; width: 300px; height: 470px;
    background: linear-gradient(200deg, var(--photo-mid) 0%, var(--photo-dark) 70%, #101012 100%);
  }
  .brand {
    position: absolute; left: 160px; top: 78px;
    display: flex; align-items: center; gap: 14px;
  }
  .brand-mark {
    width: 46px; height: 46px; background: var(--brand-green);
  }
  .brand-name {
    font-family: "Arimo", sans-serif; font-weight: 400;
    font-size: 34px; color: var(--silver-light); letter-spacing: 0.5px;
  }
  .slogan {
    position: absolute; left: 220px; top: 132px;
    font-family: "Arimo", sans-serif; font-size: 15px; line-height: 17px;
    color: var(--silver); letter-spacing: 2px;
  }
  .identity {
    position: absolute; right: 440px; top: 262px; text-align: right;
  }
  .person-name {
    font-family: "Arimo", sans-serif; font-weight: 700;
    font-size: 34px; color: var(--white); letter-spacing: 0.5px;
  }
  .person-role {
    font-family: "Open Sans", sans-serif; font-weight: 600;
    font-size: 22px; color: var(--brand-green); margin-top: 2px;
  }
  .divider {
    position: absolute; left: 400px; top: 190px;
    width: 3px; height: 150px; background: var(--white);
  }
  .contact-list {
    position: absolute; left: 424px; top: 190px; list-style: none;
  }
  .contact-list li {
    display: flex; align-items: center; gap: 12px;
    height: 30px; font-size: 19px; color: var(--white);
  }
  .contact-list svg { width: 18px; height: 18px; flex: none; }
  .accent { color: var(--brand-green); }
  .address {
    position: absolute; left: 370px; top: 402px;
    display: flex; align-items: center; gap: 8px;
    font-size: 17px; color: var(--white);
  }
  .address svg { width: 16px; height: 20px; }
</style>
</head>
<body>
<main class="canvas">
  <article class="business-card">
    <div class="ripple-texture" role="img" aria-label="Dark wave-patterned 3D wall panel surface"></div>
    <div class="interior-photo" role="img" aria-label="Dimly lit interior with a panelled feature wall"></div>

    <header class="brand">
      <span class="brand-mark"></span>
      <span class="brand-name">Ripplecraft Facades</span>
    </header>
    <p class="slogan">decorative panels for<br>interiors &amp; landscapes</p>

    <section class="identity">
      <h1 class="person-name">ADRIAN KELL</h1>
      <p class="person-role">CEO &amp; FOUNDER</p>
    </section>

    <span class="divider"></span>

    <ul class="contact-list">
      <li>
        <svg viewBox="0 0 18 18" fill="none" stroke="rgb(187,207,65)" stroke-width="1.8"><rect x="5" y="1.5" width="8" height="15" rx="1.5"/><line x1="8" y1="13.5" x2="10" y2="13.5"/></svg>
        +000 123 456 789
      </li>
      <li>
        <svg viewBox="0 0 18 18" fill="rgb(187,207,65)"><path d="M4 2l3 3-1.5 2c1 2 3 4 5 5l2-1.5 3 3-2 2.5C8 15 3 10 1.5 4z"/></svg>
        +000 123 456 789
      </li>
      <li>
        <svg viewBox="0 0 18 18" fill="rgb(187,207,65)"><rect x="5" y="1" width="8" height="5"/><rect x="2" y="7" width="14" height="8" rx="1"/><rect x="5" y="12" width="8" height="5" fill="#2a2a2c" stroke="rgb(187,207,65)" stroke-width="1.5"/></svg>
        +000 123 456 789
      </li>
      <li>
        <svg viewBox="0 0 18 18" fill="rgb(187,207,65)"><rect x="1" y="4" width="16" height="11"/><path d="M1 4l8 6 8-6" fill="none" stroke="#2a2a2c" stroke-width="1.5"/></svg>
        yourname@email.com
      </li>
      <li>
        <svg viewBox="0 0 18 18" fill="none" stroke="rgb(187,207,65)" stroke-width="2.2"><circle cx="10" cy="7" r="5"/><line x1="6.5" y1="10.5" x2="2" y2="16"/></svg>
        <span>www.<span class="accent">websitename</span>.com</span>
      </li>
    </ul>

    <p class="address">
      <svg viewBox="0 0 16 20" fill="rgb(187,207,65)"><path d="M8 0a7 7 0 0 1 7 7c0 5-7 13-7 13S1 12 1 7a7 7 0 0 1 7-7z"/><circle cx="8" cy="7" r="2.6" fill="#2a2a2c"/></svg>
      Your Street Address, New York, 1234
    </p>
  </article>
</main>
</body>
</html>
```